Moravel Aesthetic Doctor

I require an elegant, luxurious looking business card for my aesthetic business. I am a doctor and that will set me aside from competitors. I am planning to provide home and spa based treatments to clients with high expectations. I have attached my logo.

```html
<!DOCTYPE html>
<html lang="en">
<head>
<meta charset="utf-8">
<title>Moravel Aesthetic Doctor — Business Card</title>
<link rel="stylesheet" href="https://fonts.googleapis.com/css2?family=Arimo:wght@400;700&display=swap">
<style>
  :root {
    --backdrop: #2a2a2c;
    --card-grey: #a7a8ab;
    --card-white: #ffffff;
    --ink-grey: #8e8f92;
    --ink-dark: #5a5b5e;
    --sky: #4fb3e6;
    --sky-deep: #2a8fd0;
    --white: #ffffff;
  }
  * { box-sizing: border-box; margin: 0; padding: 0; }
  html, body { width: 1200px; height: 1040px; overflow: hidden; }
  body {
    background: var(--backdrop);
    font-family: "Arimo", Arial, sans-serif;
    display: flex;
    flex-direction: column;
    align-items: center;
    justify-content: center;
    gap: 60px;
  }
  .card {
    width: 760px;
    height: 434px;
    position: relative;
    box-shadow: 0 14px 30px rgba(0,0,0,0.45);
  }
  /* Front: grey, brand and services */
  .card--front {
    background: var(--card-grey);
    border-radius: 90px 0 90px 0;
    display: flex;
    flex-direction: column;
    align-items: center;
    justify-content: center;
    color: var(--white);
    text-align: center;
  }
  .brand {
    display: flex;
    align-items: center;
    gap: 18px;
  }
  .brand__mark {
    width: 64px; height: 64px;
    border-radius: 50%;
    border: 3px solid currentColor;
    flex: none;
  }
  .brand__name {
    font-size: 44px;
    font-weight: 400;
    letter-spacing: 3px;
    line-height: 1.1;
    text-transform: uppercase;
  }
  .card--front .brand { color: var(--white); margin-bottom: 48px; }
  .tagline {
    font-size: 21px;
    letter-spacing: 1.5px;
    margin-bottom: 22px;
  }
  .services {
    font-size: 21px;
    line-height: 1.45;
    letter-spacing: 0.5px;
  }
  .services .dot { margin: 0 14px; }

  /* Back: white, contact details */
  .card--back {
    background: var(--card-white);
    border-radius: 0 90px 0 90px;
    display: flex;
    align-items: center;
    padding: 0 50px 0 56px;
  }
  .card--back .brand { color: var(--sky); width: 300px; }
  .card--back .brand__mark { width: 56px; height: 56px; border-color: var(--ink-grey); }
  .card--back .brand__name { font-size: 30px; letter-spacing: 2px; }
  .divider {
    width: 1px;
    height: 240px;
    background: var(--ink-grey);
    margin: 0 34px 0 22px;
  }
  .contact { color: var(--ink-dark); }
  .contact__name {
    font-size: 30px;
    font-weight: 700;
    color: var(--ink-grey);
  }
  .contact__post {
    font-size: 17px;
    color: var(--sky);
    font-weight: 400;
    margin-left: 6px;
  }
  .contact__role {
    font-size: 22px;
    color: var(--sky);
    line-height: 1.2;
    margin: 4px 0 18px;
  }
  .contact__list { list-style: none; }
  .contact__item {
    display: flex;
    align-items: center;
    gap: 12px;
    font-size: 22px;
    line-height: 1.5;
  }
  .contact__item svg { width: 22px; height: 22px; flex: none; }
  .social { display: flex; gap: 10px; margin-top: 14px; }
  .social__dot { width: 26px; height: 26px; border-radius: 50%; }
  .social__dot--a { background: #3b5ba8; }
  .social__dot--b { background: #c13584; }
</style>
</head>
<body>

  <section class="card card--front" aria-label="Card front">
    <div class="brand">
      <span class="brand__mark" aria-hidden="true"></span>
      <span class="brand__name">Moravel Aesthetic Doctor</span>
    </div>
    <p class="tagline">HOME AND SPA BASED TREATMENTS</p>
    <p class="services">
      Dermal injectables<span class="dot">•</span>Plasma facials<span class="dot">•</span>Microneedling<br>
      Skin boosters<span class="dot">•</span>Excessive sweating
    </p>
  </section>

  <section class="card card--back" aria-label="Card back">
    <div class="brand">
      <span class="brand__mark" aria-hidden="true"></span>
      <span class="brand__name">Moravel Aesthetic Doctor</span>
    </div>
    <span class="divider" aria-hidden="true"></span>
    <div class="contact">
      <h1 class="contact__name">Dr Elise Varga<span class="contact__post">MRCPCH MD</span></h1>
      <p class="contact__role">Australasian Diploma of<br>Aesthetic Medicine</p>
      <ul class="contact__list">
        <li class="contact__item">
          <svg viewBox="0 0 24 24" aria-hidden="true"><path d="M6.6 10.8c1.4 2.8 3.8 5.1 6.6 6.6l2.2-2.2c.3-.3.7-.4 1-.2 1.1.4 2.3.6 3.6.6.6 0 1 .4 1 1V20c0 .6-.4 1-1 1C10.6 21 3 13.4 3 4c0-.6.4-1 1-1h3.5c.6 0 1 .4 1 1 0 1.3.2 2.5.6 3.6.1.3 0 .7-.2 1z" fill="var(--sky)"/></svg>
          0800 555 014
        </li>
        <li class="contact__item">
          <svg viewBox="0 0 24 24" aria-hidden="true"><rect x="2" y="5" width="20" height="14" fill="none" stroke="var(--sky)" stroke-width="2"/><path d="M2 5l10 8 10-8" fill="none" stroke="var(--sky)" stroke-width="2"/></svg>
          elise@moravel.co.nz
        </li>
        <li class="contact__item">
          <svg viewBox="0 0 24 24" aria-hidden="true"><g fill="none" stroke="var(--sky)" stroke-width="1.6"><circle cx="12" cy="12" r="9"/><ellipse cx="12" cy="12" rx="4" ry="9"/><path d="M3 12h18M5 7h14M5 17h14"/></g></svg>
          www.moravel.co.nz
        </li>
      </ul>
      <div class="social" aria-hidden="true">
        <span class="social__dot social__dot--a"></span>
        <span class="social__dot social__dot--b"></span>
      </div>
    </div>
  </section>

</body>
</html>
```